FinTech company looking to revamp and expand client-facing interface for our financial models

Pellworth Engines currently has a very simple website that allows clients to interact with our financial models. We are looking to completely redesign the current site and add several extra pages to provide extra functionality. We want the design to have a modern, slick feel, that will work on both a desktop or a tablet. It should be straightforward for clients to move between different pages at any time, and clear from the layout how to interact with the more advanced features. We have included screenshots of existing pages in the attached design brief, as well as sketches of the functionality required by the new pages, but can't provide a direct link to the current site.
Target Market(s)
Professional investors that will be paying to access the interface
Industry/Entity Type
Finance
Number of Pages Required
4 page
Colors
Designer to choose colors to be used in the design.
Look and feel
Each slider illustrates characteristics of the customer's brand and the style your logo design should communicate.

```html
<!DOCTYPE html>
<html lang="en">
<head>
<meta charset="utf-8">
<title>Pellworth Engines – Model Dashboard</title>
<link href="https://fonts.googleapis.com/css2?family=Lato:wght@400;700&display=swap" rel="stylesheet">
<style>
:root{
  --stage:#a5a5a5;
  --page:#e2e2e2;
  --card:#ffffff;
  --head-top:#16879f;
  --head-bottom:#0d4d79;
  --accent:#ef8e1c;
  --ink:#1b5f8b;
  --text:#6d6d6d;
  --line:#cfcfcf;
  --stripe:#f5f5f5;
}
*{box-sizing:border-box;margin:0;padding:0}
html,body{width:842px;height:1200px;overflow:hidden}
body{background:var(--stage);font-family:"Lato",sans-serif;position:relative}
.screen{position:absolute;left:56.5px;width:733px;height:522.7px;background:var(--page)}
.screen--models{top:51.7px}
.screen--factors{top:611.6px}
.topbar{position:relative;height:67.4px;background:linear-gradient(180deg,var(--head-top),var(--head-bottom));color:#fff}
.brand{position:absolute;left:37.5px;top:18px;font-size:20px;font-weight:700;letter-spacing:.2px}
.screen--factors .brand{left:41px}
.horizons{position:absolute;top:23px;left:192.8px;display:flex;gap:17.5px;font-size:12px}
.menu{position:absolute;top:27px;left:475.5px;display:flex;font-size:10px;align-items:center}
.menu span{padding:0 9.5px;border-left:1px solid rgba(255,255,255,.45);line-height:11px}
.menu span:first-child{border-left:none;padding-left:0}
.panel{position:absolute;left:32.9px;width:667.5px;height:397px;background:var(--card)}
.screen--models .panel{top:76.3px}
.screen--factors .panel{top:89.4px}
.field{position:absolute}
.field label{display:block;color:var(--ink);font-size:10.6px;height:16px}
.field .input{margin-top:7.5px;height:27.7px;border:1px solid var(--line);color:var(--text);font-size:10.5px;line-height:26px;padding-left:9px}
.export{position:absolute;width:58px;height:22.5px;border:1px solid var(--ink);border-radius:12px;color:var(--ink);font-size:9px;display:flex;align-items:center;justify-content:center;gap:2px}
.export svg{width:10px;height:8px}
.grid{position:absolute;border-collapse:collapse;table-layout:fixed;border:1px solid var(--line);border-top:none;color:var(--text)}
.grid th{background:var(--accent);color:#fff;font-weight:700;text-align:left;height:32px;padding:0}
.grid td{padding:0;font-size:8.4px;line-height:10px}
.grid tbody tr:nth-child(even) td{background:var(--stripe)}
.grid th:first-child,.grid td:first-child{padding-left:13.6px}
.grid--models th{font-size:8px}
.grid--models td{height:31.4px}
.grid--factors th{font-size:10.5px}
.grid--factors td{height:31.4px;font-size:9.2px}
.grid--factors th:first-child,.grid--factors td:first-child{padding-left:17px}
.chev{display:inline-block;width:8px;height:5px;margin-left:3px;vertical-align:middle}
</style>
</head>
<body>

<section class="screen screen--models">
  <header class="topbar">
    <div class="brand">PELLWORTH</div>
    <nav class="horizons"><span>250D</span><span>83D</span><span>42D</span></nav>
    <nav class="menu"><span>MODELS</span><span>SENSITIVITES</span><span>FAVORITES</span></nav>
  </header>
  <div class="panel">
    <div class="field" style="left:32.4px;top:30px;width:175px"><label>Quality Threshold</label><div class="input">-10</div></div>
    <div class="field" style="left:222.6px;top:30px;width:175px"><label>Abs. stat Threshold</label><div class="input">-10</div></div>
    <div class="export" style="left:567px;top:85.8px"><svg viewBox="0 0 10 8"><path d="M6 0l4 3.5L6 7V5C3 5 1.5 6 0 8c.5-3.5 2.5-5.5 6-5.8z" fill="currentColor"/></svg>Export</div>
    <table class="grid grid--models" style="left:27.6px;top:121.8px;width:608px">
      <colgroup><col style="width:59.6px"><col style="width:62.2px"><col style="width:60.6px"><col style="width:49.7px"><col style="width:42.9px"><col style="width:40.2px"><col style="width:45.5px"><col style="width:43.9px"><col style="width:46.5px"><col style="width:44.4px"><col style="width:45.5px"><col style="width:66.9px"></colgroup>
      <thead><tr><th style="padding-left:18px">ID<svg class="chev" viewBox="0 0 8 5"><path d="M.5.5L4 4 7.5.5" fill="none" stroke="#fff" stroke-width="1.2"/></svg></th><th>SECTOR</th><th>TIME</th><th>QUALITY</th><th>STAT 1</th><th>STAT 2</th><th>STAT 3</th><th>STAT 4</th><th>STAT 5</th><th>STAT 6</th><th>STAT 7</th><th>STAT 8</th></tr></thead>
      <tbody>
        <tr><td>Mode 1</td><td>Materials</td><td>2019-07-03<br>12:15:00</td><td>30.2288</td><td>2.60858</td><td>2.60858</td><td>2.60858</td><td>2.60858</td><td>2.60858</td><td>2.60858</td><td>2.60858</td><td>2.60858</td></tr>
        <tr><td>Model 2</td><td>Industrials</td><td>2019-07-03<br>12:15:00</td><td>32.8694</td><td>6.80646</td><td>6.80646</td><td>6.80646</td><td>6.80646</td><td>6.80646</td><td>6.80646</td><td>6.80646</td><td>6.80646</td></tr>
        <tr><td>Model 3</td><td>Consumer<br>Discretionary</td><td>2019-07-03<br>12:15:00</td><td>1.66002</td><td>4.69146</td><td>4.69146</td><td>4.69146</td><td>4.69146</td><td>4.69146</td><td>4.69146</td><td>4.69146</td><td>4.69146</td></tr>
        <tr><td>Model 4</td><td>Information<br>Technology</td><td>2019-07-03<br>12:15:00</td><td>45.6856</td><td>3.85106</td><td>3.85106</td><td>3.85106</td><td>3.85106</td><td>3.85106</td><td>3.85106</td><td>3.85106</td><td>3.85106</td></tr>
        <tr><td>Model 5</td><td>Information<br>Technology</td><td>2019-07-03<br>12:15:00</td><td>75.7733</td><td>3.34927</td><td>3.34927</td><td>3.34927</td><td>3.34927</td><td>3.34927</td><td>3.34927</td><td>3.34927</td><td>3.34927</td></tr>
      </tbody>
    </table>
  </div>
</section>

<section class="screen screen--factors">
  <header class="topbar">
    <div class="brand">PELLWORTH</div>
    <nav class="horizons"><span>250D</span><span>83D</span><span>42D</span></nav>
    <nav class="menu"><span>MODELS</span><span>SENSITIVITES</span><span>FAVORITES</span></nav>
  </header>
  <div class="panel">
    <div class="field" style="left:42.3px;top:36px;width:188.7px"><label>Stat 1 Threshold</label><div class="input">-10</div></div>
    <div class="field" style="left:246.7px;top:36px;width:188.7px"><label>Stat 2 Threshold</label><div class="input">-10</div></div>
    <div class="field" style="left:450px;top:36px;width:188.7px"><label>Stat 3 Threshold1</label><div class="input">-10</div></div>
    <div class="export" style="left:581.6px;top:94px"><svg viewBox="0 0 10 8"><path d="M6 0l4 3.5L6 7V5C3 5 1.5 6 0 8c.5-3.5 2.5-5.5 6-5.8z" fill="currentColor"/></svg>Export</div>
    <table class="grid grid--factors" style="left:37.1px;top:123.8px;width:604.8px">
      <colgroup><col style="width:100.4px"><col style="width:66.9px"><col style="width:84.2px"><col style="width:59.6px"><col style="width:60.1px"><col style="width:59.6px"><col style="width:59.6px"><col style="width:59.6px"><col style="width:54.8px"></colgroup>
      <thead><tr><th style="padding-left:18.3px">FACTOR</th><th>ID<svg class="chev" viewBox="0 0 8 5"><path d="M.5.5L4 4 7.5.5" fill="none" stroke="#fff" stroke-width="1.2"/></svg></th><th>SECTOR</th><th>STAT 1</th><th>STAT 2</th><th>STAT 3</th><th>STAT 4</th><th>STAT 5</th><th>STAT 6</th></tr></thead>
      <tbody>
        <tr><td>Factor 1</td><td>Model 1</td><td>Materials</td><td>-1.4</td><td>0.1</td><td>-3.1</td><td>-3.1</td><td>0.1</td><td>-1.4</td></tr>
        <tr><td>Factor 2</td><td>Model 1</td><td>Materials</td><td>2.8</td><td>0.1</td><td>6.1</td><td>6.1</td><td>0.1</td><td>2.8</td></tr>
        <tr><td>Factor 3</td><td>Model 1</td><td>Materials</td><td>-3.7</td><td>2.7</td><td>-7.2</td><td>-7.2</td><td>2.7</td><td>-3.7</td></tr>
        <tr><td>Factor 1</td><td>Model 2</td><td>Materials</td><td>2.8</td><td>0.2</td><td>2.7</td><td>2.7</td><td>0.2</td><td>2.8</td></tr>
        <tr><td>Factor 2</td><td>Model 2</td><td>Materials</td><td>0.8</td><td>0.3</td><td>2.5</td><td>2.5</td><td>0.3</td><td>0.8</td></tr>
      </tbody>
    </table>
  </div>
</section>

</body>
</html>
```